Website design for legal tech start up in Switzerland (B2B)

We are for a legal tech start up in Switzerland called KOVA. We have been running since August 2016. This will be our first live website.

We need a website designed and business card design for our start-up in Switzerland. We also need the Web design to be converted into HTML and CSS files.

Function of website:
• To inform potential customers of our services
• Form a key part of our digital marketing and sales footprint.
• Branding

Please find attached logo.
Updates

Project Deadline Extended Reason: Giving us time to review submissions and provide opportunity for more submissions. Added Thursday, February 16, 2017

Project Deadline Extended
Reason: Looking for more idea's not necessarily set on blue and grey colours only.

Target Market(s)

B2B tech powered legal services.

Industry/Entity Type

Legal

Contact Information for Business Card

Lean and slick design.

Coding

Coded - Design and coding required

Number of Pages Required

5+ page

Requirements
Must have
• VERY LEAN AND CLEAN DESIGN!
• We have received many great standard designs, but we are looking for something more out-of-the box: You can get inspiration from these designs: http://www.pixelvane.com/websites/clean/
• Thanks!!
• Easy content management system
• Well structured coding for additional development
• Responsive webpage for all types of devices
• SEO optimized
• Tabs (Home, services, team, careers, blog, contact us)
• Colour scheme complementary to logo
Nice to have
• Look and Design - Approachable, High-tech, Modern
• Easy to add chat bot capability in future
Should not have
• Too busy/ too much clutter
• Not take to long to load

```html
<!DOCTYPE html>
<html lang="en">
<head>
<meta charset="utf-8">
<title>KOVA – Legal Advisor</title>
<link rel="stylesheet" href="https://fonts.googleapis.com/css2?family=Lato:wght@300;400;700;900&display=swap">
<style>
:root{
  --navy:#1f3a6e;
  --navy-dark:#152a52;
  --ink:#2b2b2b;
  --text:#555a60;
  --muted:#8a8f96;
  --line:#d9dce0;
  --card:#ebedef;
  --white:#ffffff;
  --footer:#1b1f27;
}
*{box-sizing:border-box;margin:0;padding:0}
html,body{width:1200px;height:5279px;overflow:hidden}
body{font-family:'Lato',sans-serif;color:var(--text);background:var(--white);font-size:14px;line-height:1.55}
section,header,footer{position:relative;width:1200px;overflow:hidden}
.abs{position:absolute}
.photo{position:absolute;inset:0}

/* header */
.site-header{height:78px;background:var(--white)}
.brand{position:absolute;left:80px;top:18px;font-weight:900;font-size:38px;letter-spacing:2px;color:var(--navy);line-height:42px}
.header-phone{position:absolute;right:130px;top:27px;display:flex;align-items:center;gap:10px;font-size:18px;color:var(--ink);font-weight:700}
.icon-circle{width:26px;height:26px;border-radius:50%;background:var(--ink);display:flex;align-items:center;justify-content:center}
.menu-btn{position:absolute;right:78px;top:22px;width:38px;height:34px;background:var(--ink);padding:9px 8px;display:flex;flex-direction:column;justify-content:space-between}
.menu-btn span{height:3px;background:var(--white)}

/* hero */
.hero{height:549px}
.hero .photo{background:linear-gradient(90deg,#2a3242 0%,#4a5a78 35%,#8aa2c6 60%,#c8d6ea 80%,#6e86ad 100%)}
.hero-title{position:absolute;left:80px;top:208px;color:var(--white);font-size:38px;font-weight:400;line-height:48px;letter-spacing:1px}
.btn-outline{position:absolute;left:80px;top:343px;border:2px solid var(--white);color:var(--white);font-size:16px;font-weight:700;padding:14px 22px;letter-spacing:.5px}

/* headings */
.section-title{text-align:center;color:var(--ink);font-size:38px;font-weight:400;letter-spacing:1.5px}
.section-title b{font-weight:900;color:var(--navy)}
.title-rule{position:relative;width:560px;height:16px;margin:6px auto 0}
.title-rule:before{content:"";position:absolute;left:0;right:0;top:8px;border-top:1px solid var(--line)}
.title-rule span{position:absolute;left:272px;top:0;width:16px;height:16px;background:var(--white);color:var(--muted);font-size:14px;line-height:14px;text-align:center}

/* about */
.about{height:429px;background:linear-gradient(180deg,#f2f3f5,#ffffff 40%)}
.about .section-title{padding-top:20px}
.about-copy{width:1060px;margin:34px auto 0;text-align:center;font-size:15px;line-height:26px}
.mv-card{position:absolute;top:281px;width:404px;height:123px;background:var(--white);box-shadow:0 2px 8px rgba(0,0,0,.12);padding:22px 24px 0 128px}
.mv-card .ico{position:absolute;left:24px;top:22px;width:80px;height:80px;background:var(--navy);display:flex;align-items:center;justify-content:center}
.mv-card h3{color:var(--ink);font-size:19px;font-weight:700}
.mv-card p{font-size:12px;line-height:17px;margin-top:4px}

/* services */
.services{height:880px;background:var(--white)}
.services .section-title{padding-top:55px}
.services-intro{width:1000px;margin:26px auto 0;text-align:center;font-size:15px;line-height:26px}
.services-intro a{color:var(--navy);font-weight:700;text-decoration:none}
.svc{position:absolute;width:286px;height:266px;background:var(--card);text-align:center;padding-top:26px;box-shadow:0 1px 4px rgba(0,0,0,.08)}
.svc.active{background:var(--navy);color:#dfe6f3}
.svc .ico{width:82px;height:82px;margin:0 auto;background:var(--white);border:6px solid #c9ced6;display:flex;align-items:center;justify-content:center}
.svc.active .ico{border-color:#4a6296}
.svc h3{font-size:18px;font-weight:400;color:var(--ink);margin-top:38px}
.svc.active h3{color:var(--white)}
.svc p{font-size:13px;line-height:19px;width:190px;margin:6px auto 0}
.svc .toggle{position:absolute;left:128px;bottom:-15px;width:30px;height:30px;border-radius:50%;background:var(--ink);color:var(--white);font-size:20px;line-height:28px;font-weight:700}
.svc:after{content:"";position:absolute;left:0;right:0;bottom:0;height:3px;background:var(--ink)}

/* advice band */
.advice{height:370px}
.advice .photo{background:linear-gradient(90deg,#2a2a2a,#707070 30%,#9a9a9a 55%,#5a5a5a 80%,#2e2e2e)}
.advice-box{position:absolute;left:387px;top:70px;width:429px;height:229px;background:rgba(31,58,110,.93);padding:26px 34px;color:var(--white)}
.advice-box h3{font-size:26px;font-weight:400;letter-spacing:1px}
.adv-row{display:flex;align-items:center;gap:16px;margin-top:14px}
.adv-row .circ{width:44px;height:44px;border-radius:50%;background:var(--white);display:flex;align-items:center;justify-content:center;flex:none}
.adv-row span{font-size:22px}
.adv-or{font-size:22px;font-weight:700;margin:6px 0 0 166px}
.adv-row small{display:block;font-size:12px;color:#b8c4dc}

/* why choose */
.why{height:623px;background:var(--white)}
.why .section-title{padding-top:60px}
.why-col{position:absolute;top:176px;width:334px}
.why-col h4{font-size:18px;font-weight:700;color:var(--ink)}
.why-col .sub{font-size:12px;color:var(--muted);margin-top:2px}
.why-img{margin-top:10px;height:186px}
.post-card{background:var(--white);box-shadow:0 2px 8px rgba(0,0,0,.14);padding:18px 20px 22px;position:relative}
.date{position:absolute;left:20px;top:18px;width:40px;height:44px;background:var(--navy);color:var(--white);text-align:center;font-size:16px;font-weight:700;line-height:26px}
.date small{display:block;background:var(--white);color:var(--navy);font-size:10px;line-height:16px;border:1px solid var(--line)}
.post-card h5{margin-left:56px;font-size:15px;font-weight:400;color:var(--ink)}
.post-card .meta{margin-left:56px;font-size:12px;color:var(--muted)}
.post-card p{font-size:12px;line-height:18px;margin-top:10px}
.post-card .more{position:absolute;left:50%;bottom:-13px;margin-left:-13px;width:26px;height:26px;border-radius:50%;background:var(--navy)}
.dots{position:absolute;left:0;right:0;display:flex;justify-content:center;gap:8px}
.dots i{width:10px;height:10px;border-radius:50%;border:1px solid var(--navy)}
.dots i.on{background:var(--navy)}

/* blog band */
.blog-band{height:373px}
.blog-band .photo{background:linear-gradient(180deg,#bfbfbf 0%,#8a8a8a 40%,#3a3a3a 100%)}
.band-box{position:absolute;left:387px;width:429px;background:rgba(31,58,110,.93);color:var(--white);text-align:center;padding:24px 30px}
.band-box h3{font-size:26px;font-weight:400;letter-spacing:1px}
.band-box p{font-size:13px;line-height:20px;color:#d4dcec;margin-top:14px}

/* blog cards */
.blog{height:359px;background:var(--white)}
.blog-card{position:absolute;top:24px;width:330px;box-shadow:0 2px 8px rgba(0,0,0,.14);background:var(--white)}
.blog-card .img{height:186px}
.blog-card .post-card{box-shadow:none}

/* testimonials */
.testi-band{height:457px}
.testi-band .photo{background:linear-gradient(135deg,#3c3c3c,#6f6f6f 30%,#4a4a4a 55%,#8a8a8a 80%,#3a3a3a)}
.testimonials{height:388px;background:var(--white)}
.quote{position:absolute;top:36px;width:510px;height:190px;border:1px solid var(--line);box-shadow:0 2px 6px rgba(0,0,0,.08);padding:26px 36px 0 80px;font-size:13px;line-height:20px;font-style:italic}
.quote .qm{position:absolute;left:30px;top:10px;font-size:60px;color:#c4c8ce;font-family:Georgia,serif;font-style:normal}
.quote:after{content:"";position:absolute;left:70px;bottom:-12px;width:22px;height:22px;background:var(--white);border-right:1px solid var(--line);border-bottom:1px solid var(--line);transform:rotate(45deg)}
.avatar{position:absolute;top:250px;width:112px;height:112px}
.person{position:absolute;top:300px;font-size:15px;color:var(--ink)}
.person .stars{color:var(--ink);letter-spacing:2px;font-size:14px}
.arrow{position:absolute;top:118px;color:#b9bec5;font-size:22px}

/* callback */
.callback{height:288px;background:var(--navy);color:var(--white)}
.cb-title{position:absolute;left:90px;top:52px;font-size:34px;line-height:40px;font-weight:400}
.cb-copy{position:absolute;left:90px;top:150px;width:330px;font-size:13px;line-height:19px;color:#d0d9ea}
.cb-label{position:absolute;left:458px;top:40px;font-size:14px}
.field{position:absolute;height:42px;width:317px;background:var(--white);color:var(--muted);font-size:12px;padding:13px 14px}
.submit{position:absolute;left:458px;top:192px;background:var(--ink);color:var(--white);font-size:13px;font-weight:700;letter-spacing:1px;padding:10px 20px}

/* footer */
.site-footer{height:485px;color:#c9ced6}
.site-footer .photo{background:linear-gradient(180deg,#141821 0%,#1e2533 55%,#2b3447 80%,#1a1e27 100%)}
.contact-row{position:absolute;top:40px;left:0;right:0;display:flex;justify-content:space-around;font-size:13px;text-align:center}
.contact-row div{width:330px}
.contact-row svg{display:block;margin:0 auto 14px}
.foot-brand{position:absolute;left:0;right:0;top:140px;text-align:center;font-size:50px;font-weight:900;letter-spacing:4px;color:var(--white)}
.foot-copy{position:absolute;left:330px;width:540px;top:222px;text-align:center;font-size:13px;line-height:19px}
.hours{position:absolute;left:0;right:0;top:290px;display:flex;justify-content:center;gap:60px;font-size:12px;font-weight:700;color:var(--white)}
.foot-btn{position:absolute;left:538px;top:360px;border:1px solid var(--white);color:var(--white);font-size:13px;font-weight:700;padding:6px 14px;letter-spacing:.5px}
.copybar{position:absolute;left:0;right:0;bottom:0;height:69px;background:#101319;padding:0 80px;display:flex;align-items:center;justify-content:space-between;font-size:13px}
.social{display:flex;gap:12px}
.social i{width:30px;height:30px;border-radius:50%;background:var(--navy)}
</style>
</head>
<body>

<header class="site-header">
  <div class="brand">KOVA</div>
  <div class="header-phone">
    <span class="icon-circle"><svg width="14" height="14" viewBox="0 0 24 24"><path fill="#fff" d="M6.6 10.8a15 15 0 0 0 6.6 6.6l2.2-2.2c.3-.3.7-.4 1-.2 1.1.4 2.3.6 3.6.6.6 0 1 .4 1 1V20c0 .6-.4 1-1 1A17 17 0 0 1 3 4c0-.6.4-1 1-1h3.5c.6 0 1 .4 1 1 0 1.3.2 2.5.6 3.6.1.3 0 .7-.2 1z"/></svg></span>
    +41 44 555 0190
  </div>
  <div class="menu-btn"><span></span><span></span><span></span></div>
</header>

<section class="hero">
  <div class="photo" role="img" aria-label="City skyline of glass office towers at dusk"></div>
  <h1 class="hero-title">WE ARE EXPERT IN<br>LEGAL ADVISOR</h1>
  <div class="btn-outline">GET A FREE CONSULTATION</div>
</section>

<section class="about">
  <h2 class="section-title">ABOUT <b>KOVA</b></h2>
  <div class="title-rule"><span>×</span></div>
  <p class="about-copy">We bring legal expertise and modern technology together so that businesses can move fast with confidence. Our team of lawyers and engineers builds tools that turn complex regulation into clear, practical answers. From contracts to compliance, we help companies across Switzerland handle legal work in a simpler, faster and more transparent way. Every service we offer is designed around the needs of growing teams, with fixed pricing, quick turnaround and direct access to qualified advisors whenever questions arise.</p>
  <div class="mv-card" style="left:176px">
    <div class="ico"><svg width="40" height="40" viewBox="0 0 40 40" fill="#fff"><circle cx="20" cy="13" r="6"/><circle cx="9" cy="16" r="4"/><circle cx="31" cy="16" r="4"/><path d="M9 32c0-7 5-11 11-11s11 4 11 11z"/><path d="M1 30c0-5 3-8 8-8 2 0 3 .4 4 1-2 2-3 4-3 7zM39 30c0-5-3-8-8-8-2 0-3 .4-4 1 2 2 3 4 3 7z"/></svg></div>
    <h3>Our Mission</h3>
    <p>Making reliable legal support simple, fast and affordable for every business we serve.</p>
  </div>
  <div class="mv-card" style="left:620px">
    <div class="ico"><svg width="40" height="40" viewBox="0 0 40 40" fill="none" stroke="#fff" stroke-width="3"><circle cx="20" cy="20" r="15"/><circle cx="20" cy="20" r="8"/><circle cx="20" cy="20" r="2" fill="#fff"/><path d="M22 18l12-12"/></svg></div>
    <h3>Our Vision</h3>
    <p>A future where legal clarity is built into every business decision from day one.</p>
  </div>
</section>

<section class="services">
  <h2 class="section-title">OUR SERVICES</h2>
  <div class="title-rule"><span>×</span></div>
  <p class="services-intro">We were also the first to realize that the real estate world was changing, and we needed to change with it to continue innovating. Now we are investors, founders and developers behind some of the most intriguing companies in the business. <a>Contact us</a> to learn more.</p>

  <div class="svc active" style="left:130px;top:246px">
    <div class="ico"><svg width="40" height="40" viewBox="0 0 40 40" fill="var(--navy)"><path d="M20 4 4 14h32z"/><rect x="7" y="16" width="4" height="14"/><rect x="15" y="16" width="4" height="14"/><rect x="23" y="16" width="4" height="14"/><rect x="31" y="16" width="4" height="14"/><rect x="4" y="32" width="32" height="4"/></svg></div>
    <h3>Information Management</h3>
    <p>Secure storage and smart search for all your legal records.</p>
    <div class="toggle">−</div>
  </div>
  <div class="svc" style="left:457px;top:246px">
    <div class="ico"><svg width="40" height="40" viewBox="0 0 40 40" fill="var(--navy)"><circle cx="20" cy="12" r="7"/><path d="M6 36c0-9 6-14 14-14s14 5 14 14z"/></svg></div>
    <h3>Case Support</h3>
    <p>Dedicated guidance from first review to final resolution.</p>
    <div class="toggle">+</div>
  </div>
  <div class="svc" style="left:784px;top:246px">
    <div class="ico"><svg width="40" height="40" viewBox="0 0 40 40" fill="none" stroke="var(--navy)" stroke-width="3"><rect x="4" y="7" width="32" height="22"/><path d="M14 35h12M20 29v6M15 15l-4 3 4 3M25 15l4 3-4 3"/></svg></div>
    <h3>Application Development</h3>
    <p>Custom legal tools built around your existing workflow.</p>
    <div class="toggle">+</div>
  </div>
  <div class="svc" style="left:130px;top:556px">
    <div class="ico"><svg width="40" height="40" viewBox="0 0 40 40" fill="var(--navy)"><path d="M20 3 10 18h6L8 30h10v7h4v-7h10l-8-12h6z"/></svg></div>
    <h3>Environmental Litigation</h3>
    <p>Clear advice on permits, disputes and compliance duties.</p>
    <div class="toggle">+</div>
  </div>
  <div class="svc" style="left:457px;top:556px">
    <div class="ico"><svg width="40" height="40" viewBox="0 0 40 40" fill="none" stroke="var(--navy)" stroke-width="3"><circle cx="17" cy="17" r="10"/><path d="M25 25l10 10"/><path d="M12 17h10M17 12v10"/></svg></div>
    <h3>Legal Word Processing</h3>
    <p>Fast drafting and review of contracts and documents.</p>
    <div class="toggle">+</div>
  </div>
  <div class="svc" style="left:784px;top:556px">
    <div class="ico"><svg width="40" height="40" viewBox="0 0 40 40" fill="var(--navy)"><rect x="16" y="4" width="8" height="8"/><rect x="4" y="28" width="8" height="8"/><rect x="16" y="28" width="8" height="8"/><rect x="28" y="28" width="8" height="8"/><path d="M19 12h2v6h11v10h-2v-8H21v8h-2v-8h-9v8H8V18h11z"/></svg></div>
    <h3>Procurement Support</h3>
    <p>Structured sourcing, tenders and supplier agreements.</p>
    <div class="toggle">+</div>
  </div>
</section>

<section class="advice">
  <div class="photo" role="img" aria-label="Black and white photo of business people shaking hands"></div>
  <div class="advice-box">
    <h3>NEED A LEGAL ADVICE ?</h3>
    <div class="adv-row">
      <span class="circ"><svg width="22" height="22" viewBox="0 0 24 24" fill="var(--navy)"><circle cx="12" cy="7" r="5"/><path d="M3 22c0-6 4-9 9-9s9 3 9 9z"/></svg></span>
      <span>Get A FREE CONSULTATION</span>
    </div>
    <div class="adv-or">OR</div>
    <div class="adv-row" style="margin-top:4px">
      <span class="circ"><svg width="20" height="20" viewBox="0 0 24 24"><path fill="var(--navy)" d="M6.6 10.8a15 15 0 0 0 6.6 6.6l2.2-2.2c.3-.3.7-.4 1-.2 1.1.4 2.3.6 3.6.6.6 0 1 .4 1 1V20c0 .6-.4 1-1 1A17 17 0 0 1 3 4c0-.6.4-1 1-1h3.5c.6 0 1 .4 1 1 0 1.3.2 2.5.6 3.6.1.3 0 .7-.2 1z"/></svg></span>
      <div><small>Call Us Today</small><span>+41 44 555 0190</span></div>
    </div>
  </div>
</section>

<section class="why">
  <h2 class="section-title">WHY CHOOSE US ?</h2>
  <div class="title-rule"><span>×</span></div>

  <div class="why-col" style="left:80px">
    <h4>Strategic Planning</h4>
    <div class="sub">Clear goals set out in plain terms</div>
    <div class="why-img" role="img" aria-label="Hand touching a glowing digital network" style="background:linear-gradient(135deg,#1e4f86,#4ea0d6 55%,#0f2c52)"></div>
    <div class="post-card">
      <div class="date">24<small>JAN</small></div>
      <h5>Planning that fits your goals.</h5>
      <div class="meta">by admin · in news, business</div>
      <p>Practical roadmaps that keep your legal work aligned with business growth.</p>
      <div class="more"></div>
    </div>
  </div>
  <div class="why-col" style="left:433px">
    <h4>Creative</h4>
    <div class="sub">Fresh answers to old problems</div>
    <div class="why-img" role="img" aria-label="Team joining puzzle pieces together" style="background:linear-gradient(135deg,#7a8fa8,#c9d3df 50%,#a0463f)"></div>
    <div class="post-card">
      <div class="date">24<small>JAN</small></div>
      <h5>New ideas for legal work.</h5>
      <div class="meta">by admin · in news, business</div>
      <p>We rethink routine processes so your team spends less time on paperwork.</p>
      <div class="more"></div>
    </div>
  </div>
  <div class="why-col" style="left:786px">
    <h4>Consulting Practice</h4>
    <div class="sub">Experts available when needed</div>
    <div class="why-img" role="img" aria-label="Desk with charts, documents and a laptop" style="background:linear-gradient(135deg,#e8e2d6,#c9b79a 50%,#8a6e52)"></div>
    <div class="post-card">
      <div class="date">24<small>JAN</small></div>
      <h5>Advice you can act on.</h5>
      <div class="meta">by admin · in news, business</div>
      <p>Direct access to lawyers who understand technology and startups.</p>
      <div class="more"></div>
    </div>
  </div>
  <div class="dots" style="top:586px"><i class="on"></i><i></i></div>
</section>

<section class="blog-band">
  <div class="photo" role="img" aria-label="Black and white city skyline"></div>
  <div class="band-box" style="top:90px">
    <h3>LATEST BLOG</h3>
    <p>News, guides and insights from our team on legal technology, regulation and running a modern business in Switzerland. Read our latest thinking below.</p>
  </div>
</section>

<section class="blog">
  <div class="blog-card" style="left:77px">
    <div class="img" role="img" aria-label="Hand touching a glowing digital network" style="background:linear-gradient(135deg,#1e4f86,#4ea0d6 55%,#0f2c52)"></div>
    <div class="post-card">
      <div class="date">24<small>JAN</small></div>
      <h5>Automating contract review.</h5>
      <div class="meta">by admin · in news, business</div>
      <p>How smart tools cut review time while keeping lawyers in control.</p>
    </div>
  </div>
  <div class="blog-card" style="left:435px">
    <div class="img" role="img" aria-label="Team joining puzzle pieces together" style="background:linear-gradient(135deg,#7a8fa8,#c9d3df 50%,#a0463f)"></div>
    <div class="post-card">
      <div class="date">24<small>JAN</small></div>
      <h5>Building a compliant startup.</h5>
      <div class="meta">by admin · in news, business</div>
      <p>Key legal steps every founder should take in the first year.</p>
    </div>
  </div>
  <div class="blog-card" style="left:793px">
    <div class="img" role="img" aria-label="Desk with charts, documents and a laptop" style="background:linear-gradient(135deg,#e8e2d6,#c9b79a 50%,#8a6e52)"></div>
    <div class="post-card">
      <div class="date">24<small>JAN</small></div>
      <h5>New data rules explained.</h5>
      <div class="meta">by admin · in news, business</div>
      <p>A short guide to what the latest privacy changes mean for you.</p>
    </div>
  </div>
  <div class="dots" style="top:312px"><i class="on"></i><i></i></div>
</section>

<section class="testi-band">
  <div class="photo" role="img" aria-label="Mosaic of many small client portraits in grey tones"></div>
  <div class="band-box" style="top:120px">
    <h3>CLIENT TESTIMONIALS</h3>
    <p>Companies of every size trust us with their legal work. Here is what some of our clients say about working with our team.</p>
  </div>
</section>

<section class="testimonials">
  <div class="arrow" style="left:22px">‹</div>
  <div class="arrow" style="right:22px">›</div>
  <div class="quote" style="left:70px"><span class="qm">“</span>Working with this team changed how we handle contracts. Reviews that once took weeks now take days, and the advice is always clear and practical. They understand startups and speak our language. We feel supported at every step and would recommend them to any growing company.</div>
  <div class="avatar" role="img" aria-label="Client portrait" style="left:90px;background:linear-gradient(160deg,#c9d2de,#7d8da3)"></div>
  <div class="person" style="left:396px">Mr. Elias Brenner<div class="stars">★★★★☆</div></div>
  <div class="quote" style="left:618px"><span class="qm">“</span>Fast, friendly and precise. The platform makes it easy to track every matter, and the lawyers are always available when questions come up. Fixed pricing gave us the confidence to plan ahead. A modern partner for a modern business, and exactly what we needed.</div>
  <div class="avatar" role="img" aria-label="Client portrait" style="left:638px;background:linear-gradient(160deg,#e3d6c4,#a8916f)"></div>
  <div class="person" style="left:944px">Mr. Elias Brenner<div class="stars">★★★★☆</div></div>
</section>

<section class="callback">
  <h2 class="cb-title">Request<br>A Call Back.</h2>
  <p class="cb-copy">Leave your details and one of our advisors will call you back within one business day to discuss your needs. [+]</p>
  <div class="cb-label">Please fill up bellow form</div>
  <div class="field" style="left:458px;top:72px">Name</div>
  <div class="field" style="left:803px;top:72px">Email</div>
  <div class="field" style="left:458px;top:128px">Phone</div>
  <div class="field" style="left:803px;top:128px">Message</div>
  <div class="submit">SUBMIT</div>
</section>

<footer class="site-footer">
  <div class="photo" role="img" aria-label="Night city skyline with lit towers"></div>
  <div class="contact-row">
    <div><svg width="18" height="22" viewBox="0 0 24 30"><path fill="#c9ced6" d="M12 0a11 11 0 0 0-11 11c0 8 11 19 11 19s11-11 11-19A11 11 0 0 0 12 0zm0 15a4 4 0 1 1 0-8 4 4 0 0 1 0 8z"/></svg>Bahnhofstrasse 24, 8001 Zürich</div>
    <div><svg width="20" height="20" viewBox="0 0 24 24"><path fill="#c9ced6" d="M6.6 10.8a15 15 0 0 0 6.6 6.6l2.2-2.2c.3-.3.7-.4 1-.2 1.1.4 2.3.6 3.6.6.6 0 1 .4 1 1V20c0 .6-.4 1-1 1A17 17 0 0 1 3 4c0-.6.4-1 1-1h3.5c.6 0 1 .4 1 1 0 1.3.2 2.5.6 3.6.1.3 0 .7-.2 1z"/></svg>Phone: +41 44 555 0191</div>
    <div><svg width="22" height="20" viewBox="0 0 24 24"><path fill="#c9ced6" d="M2 11 22 2l-6 20-5-8z"/></svg>Email: hello@kova.ch</div>
  </div>
  <div class="foot-brand">KOVA</div>
  <p class="foot-copy">Legal technology and expert advice for modern businesses across Switzerland. Clear pricing, fast answers and lawyers who understand your world.</p>
  <div class="hours"><span>MON - FRI: 8:00 - 17:00</span><span>SATURDAY: 9:00 - 15:00</span><span>SUNDAY: CLOSED</span></div>
  <div class="foot-btn">CONTACT US</div>
  <div class="copybar">
    <span>Copyright © 2016 KOVA . All Right Reserved.</span>
    <div class="social"><i></i><i></i><i></i><i></i></div>
  </div>
</footer>

</body>
</html>
```